Business Card Design Project

I need a business card designed from scratch. I have an existing logo that I can upload in Illustrator for modification or redesign.

The Company is called Query Lanterns http://querylanterns.com.au and we provide Search Engine Optimization services to Australian businesses. The current logo signifies an increase in visitors, profits etc...

There are no restrictions as to the redesign - colours, style etc are all open to change.

Cards will be full colour and one sided printed at http://www.cardmoxel.com.au so check their requirements for file format and sizes etc.

I will expect all original files upon completion of project.

Target Market(s)

Any business with a web site looking to improve their search engine rankings

Industry/Entity Type

Business

Requirements
Must have
• I like modern, sleek designs. Clean, not fussy, uncluttered.

```html
<!DOCTYPE html>
<html lang="en">
<head>
<meta charset="UTF-8">
<title>Query Lanterns – Business Card</title>
<link rel="stylesheet" href="https://fonts.googleapis.com/css2?family=Source+Sans+3:wght@400;600;700&display=swap">
<style>
  :root {
    --backdrop: #b88a1c;
    --card-white: #ffffff;
    --brand-blue: #1b6fae;
    --ink: #2a2a2a;
    --orange-deep: #ff9500;
    --orange-mid: #f8b21e;
    --yellow-glow: #f2d63e;
    --curl-dark: #2b2b2b;
    --curl-light: #5a5a5a;
  }
  * { margin: 0; padding: 0; box-sizing: border-box; }
  html, body { width: 1200px; height: 686px; overflow: hidden; }
  body {
    background: var(--backdrop);
    font-family: "Source Sans 3", Arial, sans-serif;
    position: relative;
  }
  .card {
    position: absolute;
    width: 508px;
    height: 289px;
    border-radius: 26px;
    overflow: hidden;
    box-shadow: 1px 2px 2px rgba(0,0,0,0.55);
  }
  .card-front { left: 75px; top: 146px; background: var(--card-white); }
  .card-back {
    left: 607px; top: 268px;
    background: radial-gradient(ellipse 60% 70% at 50% 50%, var(--yellow-glow) 0%, var(--orange-mid) 55%, var(--orange-deep) 100%);
  }
  .page-curl { position: absolute; left: 0; top: 0; width: 508px; height: 289px; }
  .holder { position: absolute; right: 44px; top: 16px; text-align: right; color: var(--brand-blue); font-weight: 700; }
  .holder-name { font-size: 20px; line-height: 24px; }
  .holder-title { font-size: 13px; line-height: 16px; }
  .brand-name {
    position: absolute;
    color: var(--brand-blue);
    font-weight: 700;
    white-space: nowrap;
  }
  .card-front .brand-name { left: 62px; top: 112px; font-size: 34px; line-height: 40px; }
  .card-back .brand-name { left: 0; right: 0; top: 120px; text-align: center; font-size: 38px; line-height: 46px; }
  .contact-list { position: absolute; left: 170px; top: 180px; list-style: none; color: var(--ink); font-size: 13.5px; }
  .contact-list li { display: flex; align-items: center; height: 17.5px; }
  .contact-list svg { width: 11px; height: 11px; margin-right: 5px; fill: var(--brand-blue); }
  .address { position: absolute; left: 169px; top: 242px; font-size: 14px; color: var(--ink); }
</style>
</head>
<body>
  <section class="card card-front">
    <svg class="page-curl" viewBox="0 0 508 289" aria-hidden="true">
      <defs>
        <linearGradient id="foldOrange" x1="0" y1="0" x2="1" y2="0">
          <stop offset="0" stop-color="#ff9d00"/>
          <stop offset="0.55" stop-color="#f4d23a"/>
          <stop offset="1" stop-color="#ff9500"/>
        </linearGradient>
        <linearGradient id="curlShade" x1="0" y1="0" x2="1" y2="1">
          <stop offset="0" stop-color="var(--curl-dark)"/>
          <stop offset="0.6" stop-color="var(--curl-light)"/>
          <stop offset="1" stop-color="var(--curl-dark)"/>
        </linearGradient>
      </defs>
      <polygon points="208,0 508,0 508,94" fill="url(#foldOrange)"/>
      <path d="M208 0 L508 94 L508 110 Q470 118 464 161 Q390 72 208 0 Z" fill="url(#curlShade)"/>
    </svg>
    <div class="holder">
      <p class="holder-name">Your Name</p>
      <p class="holder-title">Title</p>
    </div>
    <p class="brand-name">Query Lanterns</p>
    <ul class="contact-list">
      <li><svg viewBox="0 0 12 12"><path d="M2.5 0.5 L4.5 3 L3.5 4.5 Q5 7.5 7.5 8.5 L9 7.5 L11.5 9.5 L10 11.5 Q3 11 0.5 2 Z"/></svg>123-456-7890</li>
      <li><svg viewBox="0 0 12 12"><path d="M0 2 H12 V10 H0 Z M0.8 2.6 L6 6.6 L11.2 2.6"/></svg>inquiry@querylanterns.com.au.com</li>
      <li><svg viewBox="0 0 12 12"><circle cx="6" cy="6" r="5.5"/><path d="M0.5 6 H11.5 M6 0.5 V11.5" stroke="#fff" stroke-width="0.8"/></svg>www.querylanterns.com.au</li>
    </ul>
    <p class="address">Street name City, State, zip code</p>
  </section>

  <section class="card card-back">
    <p class="brand-name">Query Lanterns</p>
  </section>
</body>
</html>
```